Business Card for beauty technology startup

Design Glimora Business Card for a Beauty, based on the website identity and colors (https://www.glimora-example.com).
Glimora is a beauty tech startup that gathers helpful product info for beauty lovers and consumers (such as availability on stores, price range and product reviews) for makeup products. The card design must be young, colorful but clean, and very modern.

Target Market(s)

woman, 15-35

Industry/Entity Type

Cosmetics

Contact Information for Business Card

Full Name, address, phone

Font styles to use
Other font styles liked:
• Advent Pro

Colors
e34297
86cfc6
ffffff
5c5c5c
e8e8e8
e667a6
b2b2b2

Requirements
Must have
• One full colored side with a creative design and another with card info
• Use Color palette: #95C5C5 and/or #D38AA5
• Use fonts: Advent Pro
• Use website identity: https://www.glimora-example.com
Nice to have
• If needed extra font: Roboto

```html
<!DOCTYPE html>
<html lang="en">
<head>
<meta charset="utf-8">
<title>Glimora Business Card</title>
<link rel="stylesheet" href="https://fonts.googleapis.com/css2?family=Advent+Pro:wght@300;400&family=Roboto:wght@300;400;500&display=swap">
<style>
  :root {
    --canvas-bg: #e8e8e8;
    --card-plum: #8d3a5d;
    --card-rose: #b9708f;
    --card-mist: #e9e1e4;
    --card-text: #ffffff;
    --card-text-soft: #f6e4ec;
    --brand-ink: #7a2e4f;
    --oval-fill: rgba(255, 255, 255, 0.62);
  }
  * { margin: 0; padding: 0; box-sizing: border-box; }
  html, body {
    width: 1200px;
    height: 969px;
    overflow: hidden;
    background: var(--canvas-bg);
  }
  .canvas {
    position: relative;
    width: 1200px;
    height: 969px;
  }
  .card {
    position: absolute;
    left: 100px;
    top: 201px;
    width: 1000px;
    height: 566px;
    border-radius: 30px;
    overflow: hidden;
    background: linear-gradient(100deg, var(--card-plum) 0%, #9a4a6c 30%, var(--card-rose) 55%, #d6b6c3 75%, var(--card-mist) 100%);
    box-shadow: 0 10px 30px rgba(0, 0, 0, 0.12);
    font-family: "Roboto", Arial, sans-serif;
    color: var(--card-text);
  }
  .brand-oval {
    position: absolute;
    left: 435px;
    top: 12px;
    width: 499px;
    height: 542px;
    border-radius: 50%;
    background: var(--oval-fill);
  }
  .brand-decor {
    position: absolute;
    left: 0;
    top: 0;
    width: 1000px;
    height: 566px;
  }
  .brand-decor .arc {
    fill: none;
    stroke: var(--brand-ink);
    stroke-width: 12;
    stroke-linecap: round;
  }
  .brand-decor .mark-spot {
    fill: none;
    stroke: var(--brand-ink);
    stroke-width: 4;
  }
  .brand-name {
    position: absolute;
    left: 462px;
    top: 326px;
    width: 500px;
    text-align: center;
    font-family: "Advent Pro", "Roboto", sans-serif;
    font-weight: 300;
    font-size: 66px;
    line-height: 76px;
    letter-spacing: 8px;
    color: var(--brand-ink);
  }
  .holder-name {
    position: absolute;
    left: 65px;
    top: 76px;
    font-size: 29px;
    font-weight: 500;
    letter-spacing: 0.5px;
  }
  .holder-role {
    position: absolute;
    left: 65px;
    top: 120px;
    font-size: 22px;
    font-weight: 400;
    color: var(--card-text-soft);
  }
  .address {
    position: absolute;
    left: 65px;
    top: 268px;
    font-size: 24px;
    font-weight: 300;
    font-style: normal;
    line-height: 31px;
  }
  .contact-list {
    position: absolute;
    left: 65px;
    top: 347px;
    list-style: none;
    font-size: 23px;
    font-weight: 300;
  }
  .contact-item {
    display: flex;
    align-items: center;
    height: 31px;
  }
  .contact-icon {
    width: 20px;
    height: 20px;
    margin-right: 20px;
    fill: var(--card-text);
  }
</style>
</head>
<body>
<main class="canvas">
  <section class="card" aria-label="Glimora business card">
    <div class="brand-oval"></div>
    <svg class="brand-decor" viewBox="0 0 1000 566" aria-hidden="true">
      <path class="arc" d="M750 4 A290 285 0 0 1 922 102"/>
      <path class="arc" d="M986 334 A290 285 0 0 1 690 570"/>
      <circle class="mark-spot" cx="714" cy="189" r="78"/>
    </svg>
    <div class="brand-name">GLIMORA</div>

    <h1 class="holder-name">CLARA VENNET</h1>
    <p class="holder-role">CEO/FOUNDER</p>

    <address class="address">
      2140 Larkspur Row<br>
      Fairbrook, Oregon 97850
    </address>

    <ul class="contact-list">
      <li class="contact-item">
        <svg class="contact-icon" viewBox="0 0 20 20" aria-hidden="true"><path d="M4 2h3l1.5 4-2 1.3a11 11 0 0 0 6.2 6.2L14 11.5l4 1.5v3a2 2 0 0 1-2 2A15 15 0 0 1 2 4a2 2 0 0 1 2-2z"/></svg>
        <span>555 214 7730</span>
      </li>
      <li class="contact-item">
        <svg class="contact-icon" viewBox="0 0 20 20" aria-hidden="true"><path d="M6 1h8a1 1 0 0 1 1 1v16a1 1 0 0 1-1 1H6a1 1 0 0 1-1-1V2a1 1 0 0 1 1-1zm1 2v12h6V3zm3 13.2a1 1 0 1 0 0 2 1 1 0 0 0 0-2z"/></svg>
        <span>555 381 6092</span>
      </li>
      <li class="contact-item">
        <svg class="contact-icon" viewBox="0 0 20 20" aria-hidden="true"><path d="M5 2h10v5H5zM2 8h16a1 1 0 0 1 1 1v6h-3v3H4v-3H1V9a1 1 0 0 1 1-1zm4 6v3h8v-3z"/></svg>
        <span>555 907 4418</span>
      </li>
      <li class="contact-item">
        <svg class="contact-icon" viewBox="0 0 20 20" aria-hidden="true"><path d="M2 5h16v10H2zm1.5 1.2v.5L10 11l6.5-4.3v-.5z"/></svg>
        <span>info@glimora-example.com</span>
      </li>
      <li class="contact-item">
        <svg class="contact-icon" viewBox="0 0 20 20" aria-hidden="true"><path d="M10 1.5a8.5 8.5 0 1 0 0 17 8.5 8.5 0 0 0 0-17zm-1 2.2v2.6L6.5 8 5 6.2a6.6 6.6 0 0 1 4-2.5zm3 .3a6.6 6.6 0 0 1 4.5 6.8L14 9.5l-2 1-1.5 3 1 3A6.6 6.6 0 0 1 4 8.5L6 10l2 1 1 3-1 2.5 2-1 1-3 2-1 .5-3-1-2z"/></svg>
        <span>www.glimora-example.com</span>
      </li>
    </ul>
  </section>
</main>
</body>
</html>
```